R7M Horizon Business Card Design

We need a business card created for our New Business "R7M Horizon"<br/><br/>The business card design is up to you however the following information must be on the business card:<br/><br/>Front of the business card -<br/>Email :darrenp@r7mhorizon.nz<br/>Mobile: +64 (0) 22 4870 619<br/>Website: www.r7mhorizon.nz<br/>Card Owner Name: Darren Paltrow<br/>Company Title: Business Development Manager<br/>Slogan: "Bright ideas, made real". <br/>Logo On the front attached to the design brief<br/><br/>On the back: <br/>Space on the back for 4 more versions of the logo across the bottom of the card indicating different subsidiary brands - R7M Coffee, R7M Arts, R7M ?? (The card will be used for all of these brands - We Will add the extra subsidiary logos to the design once the design is finished (We are a graphics design team). <br/><br/>Other than that we want a premium feeling logo that remains universally usable depending on the business entity that we are using the card for. The use of bright bold colours would be great but we still want the card to feel premium.
Target Market(s)
Gift Design and Manufacturing Companies
Contact Information for Business Card
Front of the business card -
Email :darrenp@r7mhorizon.nz
Mobile: +64 (0) 22 4870 619
Website: www.r7mhorizon.nz
Card Owner Name: Darren Paltrow
Company Title: Business Development Manager
Slogan: "Bright ideas, made real".
Logo On the front attached to the design brief

```html
<!DOCTYPE html>
<html lang="en">
<head>
<meta charset="utf-8">
<title>R7M Horizon Business Card</title>
<link rel="stylesheet" href="https://fonts.googleapis.com/css2?family=Montserrat:wght@600;700&family=Roboto:ital,wght@0,400;1,400&display=swap">
<style>
  :root {
    --brand-blue: #34449c;
    --ink-dark: #2a2a2a;
    --paper: #ffffff;
    --backdrop: #dcdcdc;
  }
  * { margin: 0; padding: 0; box-sizing: border-box; }
  html, body {
    width: 1200px; height: 802px; overflow: hidden;
    background: var(--backdrop);
  }
  .stage { position: relative; width: 1200px; height: 802px; }
  .card {
    position: absolute; top: 274px;
    width: 443px; height: 264px;
    overflow: hidden;
    box-shadow: 0 3px 6px rgba(0,0,0,0.35);
  }
  .card--front { left: 136px; background: var(--brand-blue); }
  .card--back { left: 624px; background: var(--brand-blue); }
  .front-shape { position: absolute; inset: 0; width: 100%; height: 100%; }
  .brand-name {
    position: absolute;
    font-family: "Montserrat", sans-serif;
    font-weight: 700;
    white-space: nowrap;
    letter-spacing: 0.5px;
  }
  .card--front .brand-name {
    left: 168px; top: 68px;
    font-size: 30px; color: var(--brand-blue);
  }
  .card--back .brand-name {
    left: 0; right: 0; top: 104px; text-align: center;
    font-size: 36px; color: var(--paper);
  }
  .holder-name {
    position: absolute; left: 19px; top: 169px;
    font-family: "Montserrat", sans-serif; font-weight: 700;
    font-size: 15px; color: var(--paper); letter-spacing: 0.2px;
  }
  .holder-title {
    position: absolute; left: 20px; top: 188px;
    font-family: "Roboto", sans-serif; font-size: 12.5px; color: var(--paper);
  }
  .contact-list {
    position: absolute; left: 21px; top: 214px; list-style: none;
    font-family: "Roboto", sans-serif; font-size: 12.5px; color: var(--paper);
  }
  .contact-list li { display: flex; align-items: center; gap: 3px; height: 17px; }
  .contact-icon { width: 13px; height: 13px; flex: none; }
  .slogan {
    position: absolute; left: 249px; top: 232px;
    font-family: "Roboto", sans-serif; font-style: italic;
    font-size: 12.5px; color: var(--paper); text-transform: uppercase;
    white-space: nowrap;
  }
  .website {
    position: absolute; left: 0; right: 0; top: 216px; text-align: center;
    font-family: "Roboto", sans-serif; font-size: 12.5px;
    letter-spacing: 1.6px; color: var(--paper);
  }
</style>
</head>
<body>
<main class="stage">
  <section class="card card--front">
    <svg class="front-shape" viewBox="0 0 545 325" preserveAspectRatio="none" aria-hidden="true">
      <path d="M0 121 C40 104 100 106 170 142 C250 182 330 250 412 248 C468 246 506 196 508 130"
            fill="none" stroke="var(--ink-dark)" stroke-width="6"/>
      <path d="M0 0 H435 C485 25 505 75 500 125 C495 190 460 240 410 242 C330 245 250 175 170 135 C100 100 40 100 0 115 Z"
            fill="var(--paper)"/>
    </svg>
    <div class="brand-name">R7M Horizon</div>
    <h1 class="holder-name">DARREN PALTROW</h1>
    <p class="holder-title">Business Development Manager</p>
    <ul class="contact-list">
      <li>
        <svg class="contact-icon" viewBox="0 0 14 14" aria-hidden="true">
          <rect x="0.75" y="0.75" width="12.5" height="12.5" rx="2" fill="none" stroke="#fff" stroke-width="1.2"/>
          <path d="M4.5 3.2 L6 5.2 L5.2 6.2 C5.8 7.5 6.6 8.3 7.8 8.9 L8.8 8.1 L10.8 9.5 L10 10.8 C7 10.8 3.2 7 3.2 4 Z" fill="#fff"/>
        </svg>
        <span>+64 (0) 22 4870 619</span>
      </li>
      <li>
        <svg class="contact-icon" viewBox="0 0 14 14" aria-hidden="true">
          <rect x="0.5" y="3" width="13" height="8.5" fill="#fff"/>
          <path d="M0.5 3 L7 8 L13.5 3" fill="none" stroke="var(--brand-blue)" stroke-width="1"/>
        </svg>
        <span>darrenp@r7mhorizon.nz</span>
      </li>
    </ul>
    <p class="slogan">Bright ideas, made real</p>
  </section>

  <section class="card card--back">
    <div class="brand-name">R7M Horizon</div>
    <p class="website">www.r7mhorizon.nz</p>
  </section>
</main>
</body>
</html>
```